Probate (Legal) Wordpress Design with Coding for Online Company

I need a Wordpress design with coding, pictures, content to be provided by me, fully responsive, and development. This is for a 6-7 page design.

Pages Needed: Home/About/Probate/Process/FAQ/Contact Us/Blog.

The home page should be organized as followed:
-Steps in Probate: Gather; Implement; Close (each step will come with content)
-Flat-Fee Price & Savings: Content will go here with a button to contact us (phone number) or just the phone number.
-You Have Questions, We Have Answers: five questions with content. Only one question answer to show at a time when clicked on the question from the list.
-Get to Know Us: a brief description with content about what we do and who we are.

Main image slogan: Helping Californians deal with loss with DIGNITY & UNDERSTATING (you may use a better slogan if you wish).

The Contact page should not have a map since we are an online company. We service the entire state of California in every county and city.

The About page should be simple, direct, and easy on the eye. It should have a brief description of who we are and it should have no more than 6 reasons why the client should hire us.

About our online California company. We are not attorneys but legal document assistants who prepare legal documents for probate estate when someone dies with or without a will and assets need to be distributed. We have a flat-fee for Formal Probate of $999 and $699 for Informal Probate. We are an online company and offer our services to the entire state of California in every county. We do everything over the phone and email. The turn around time for us to prepare the initial legal paperwork for the client is within 3-5 business days. We can prepare, file, serve and manage a probate matter from petition to closing. We are not attorneys so our prices are very affordable compare to the attorney.

The company name for the website will be www.velmarhollow.com, The Velmar Hollow Group.

I do not have a logo yet. The colors of the website should be easy on the eye and calming. THE SITE SHOULD BE SIMPLE AND STRAIGHT TO THE POINT. EASY TO NAVIGATE.

The company phone number should be very visible and should stand out to the client. It should also be clickable and ready to dial for smartphone users.

I do not want a contact form on the homepage. THE MAIN THING IS FOR THE POTENTIAL CLIENT TO CALL OUR OFFICE TO SIGN UP.

I do like some images of family or people since we are dealing with people who just lost a loved one. Not all the images have to be of people.

The site should not look like we practice law or that people can mistake us for attorneys.

Target Market(s)

People who just lost a loved one who had property, assets, in California but died with or without a will or trust. This is for people looking to hire non-attorneys.

Coding

Coded - Design and coding required

Font styles to use
Serif

Colors

Designer to choose colors to be used in the design.

Requirements
Must have
• Refer to Project Description.
Nice to have
• The sample images provided is what I am attracted to for the homepage image.
Should not have

```html
<!DOCTYPE html>
<html lang="en">
<head>
<meta charset="utf-8">
<title>The Velmar Hollow Group</title>
<link href="https://fonts.googleapis.com/css2?family=Oswald:wght@400;500;600&family=Lato:wght@400;700&display=swap" rel="stylesheet">
<style>
:root{
  --blue:#0b63b6;
  --blue-dark:#09549b;
  --orange:#e8a20c;
  --ink:#222;
  --muted:#666;
  --light:#f4f4f4;
  --white:#fff;
  --line:#e2e2e2;
}
*{margin:0;padding:0;box-sizing:border-box}
html,body{width:1200px;height:3416px;overflow:hidden}
body{font-family:"Lato",sans-serif;color:var(--ink);background:var(--white);position:relative}
h1,h2,h3,h4,.btn,.nav a{font-family:"Oswald",sans-serif;font-weight:500}
.btn{position:absolute;background:var(--orange);color:var(--white);font-size:13px;text-transform:uppercase;display:flex;align-items:center;justify-content:center;letter-spacing:.3px}

/* header */
.site-header{position:absolute;top:0;left:0;width:1200px;height:80px;background:var(--white)}
.brand{position:absolute;left:132px;top:27px;display:flex;align-items:center;gap:10px}
.brand-mark{width:20px;height:20px;background:var(--blue)}
.brand-name{font-family:"Lato",sans-serif;font-weight:700;font-size:20px;color:var(--ink)}
.nav{position:absolute;left:458px;top:31px;display:flex}
.nav a{font-size:14px;color:var(--ink);text-decoration:none;margin-right:36px;font-weight:400}
.nav a.active{color:var(--blue)}
.header-phone{position:absolute;left:936px;top:22px;display:flex;align-items:center;gap:10px;font-family:"Oswald",sans-serif;font-size:15px}
.phone-ring{width:36px;height:36px;border:2px solid var(--orange);border-radius:50%;display:flex;align-items:center;justify-content:center}

/* hero */
.hero{position:absolute;top:80px;left:0;width:1200px;height:489px;background:linear-gradient(180deg,#3a4a66 0%,#55617a 35%,#6a6258 65%,#2f3440 100%)}
.hero::after{content:"";position:absolute;inset:0;background:rgba(10,20,40,.35)}
.hero-text{position:absolute;z-index:2;width:1200px;text-align:center;color:var(--white)}
.hero-sub{top:142px;font-family:"Oswald",sans-serif;font-size:30px;font-weight:400}
.hero-title{top:190px;font-size:66px;font-weight:600;letter-spacing:1px}
.hero .btn{z-index:2;left:535px;top:300px;width:132px;height:41px}
.hero-arrow{position:absolute;z-index:2;top:225px;width:34px;height:38px;background:rgba(255,255,255,.75);display:flex;align-items:center;justify-content:center}

/* steps */
.steps{position:absolute;top:569px;left:0;width:1200px;height:426px;background:var(--blue);color:var(--white)}
.steps h2{position:absolute;top:56px;width:1200px;text-align:center;font-size:32px}
.step{position:absolute;top:128px;width:300px;text-align:center}
.step svg{display:block;margin:0 auto}
.step h3{font-family:"Lato",sans-serif;font-weight:700;font-size:17px;margin-top:22px}
.step .bar{width:80px;height:3px;background:var(--orange);margin:12px auto 14px}
.step p{font-size:11px;line-height:17px;padding:0 16px}
.step-divider{position:absolute;top:135px;width:1px;height:240px;background:rgba(255,255,255,.18)}

/* why */
.why{position:absolute;top:995px;left:0;width:1200px;height:645px;background:var(--white)}
.why-photo{position:absolute;left:171px;top:52px;width:341px;height:593px;background:linear-gradient(180deg,#eef0f2 0%,#d8dce0 35%,#2b2e36 60%,#1c1f26 100%);border-radius:150px 150px 0 0}
.why h2{position:absolute;left:578px;top:110px;font-size:31px}
.reason{position:absolute;left:578px;width:492px}
.reason .icon{position:absolute;left:0;top:0}
.reason h4{position:absolute;left:69px;top:0;font-size:17px;font-weight:400}
.reason p{position:absolute;left:69px;top:30px;font-size:11px;line-height:19px;color:var(--muted)}

/* flat fee */
.fee{position:absolute;top:1640px;left:0;width:1200px;height:421px;background:linear-gradient(100deg,#2b2826 0%,#4a3f38 45%,#6c5a4c 70%,#5a5a5c 100%)}
.fee::after{content:"";position:absolute;inset:0;background:rgba(0,0,0,.35)}
.fee>*{z-index:2}
.fee h2{position:absolute;left:132px;top:88px;color:var(--white);font-size:32px}
.fee p{position:absolute;left:132px;width:428px;color:var(--white);font-size:11px;line-height:20px}
.fee .btn{left:132px;top:291px;width:128px;height:39px}

/* faq */
.faq{position:absolute;top:2061px;left:0;width:1200px;height:371px;background:var(--light)}
.faq h2{position:absolute;top:62px;width:1200px;text-align:center;font-size:32px}
.q{position:absolute;background:var(--white);border:1px solid var(--line);display:flex}
.q .qi{width:46px;background:var(--orange);display:flex;align-items:flex-start;justify-content:center;padding-top:10px;flex-shrink:0}
.q.open .qi{background:var(--blue)}
.q .qb{padding:11px 14px;flex:1;position:relative}
.q .qt{font-size:13px;color:var(--ink)}
.q.open .qt{color:var(--blue)}
.q .qa{font-size:11px;line-height:18px;color:var(--muted);margin-top:6px}
.q .pm{position:absolute;right:12px;top:12px}

/* know */
.know{position:absolute;top:2432px;left:0;width:1200px;height:665px;background:var(--white)}
.know h2{position:absolute;top:78px;width:1200px;text-align:center;font-size:32px}
.know h3{position:absolute;font-size:22px;font-weight:400}
.know p{position:absolute;font-size:11px;line-height:19px;color:var(--muted)}
.circle{position:absolute;width:216px;height:216px;border-radius:50%;border:2px dashed #cfcfcf;padding:10px}
.circle div{width:100%;height:100%;border-radius:50%}

/* footer */
.footer{position:absolute;top:3097px;left:0;width:1200px;height:269px;background:var(--blue);color:var(--white)}
.fcol{position:absolute;top:52px}
.fcol h4{font-size:15px;margin-bottom:16px;letter-spacing:.4px}
.fcol li{list-style:none;font-size:11px;line-height:18px}
.fcol p{font-size:11px;line-height:18px}
.news-input{width:215px;height:40px;background:var(--white);color:#888;font-size:10px;padding:14px 12px;margin-top:22px}
.fcol .btn{position:static;width:104px;height:39px;margin-top:12px}
.contact-row{display:flex;gap:14px;align-items:flex-start;font-size:11px;margin-bottom:16px}
.bottom-bar{position:absolute;top:3366px;left:0;width:1200px;height:50px;background:var(--blue-dark);color:var(--white);font-size:10px}
.bottom-bar .copy{position:absolute;left:132px;top:19px}
.follow{position:absolute;left:846px;top:12px;display:flex;align-items:center;gap:7px}
.social{width:26px;height:26px;border-radius:50%;background:var(--white);opacity:.95}
</style>
</head>
<body>

<header class="site-header">
  <div class="brand"><span class="brand-mark"></span><span class="brand-name">The Velmar Hollow Group</span></div>
  <nav class="nav">
    <a class="active">Home</a><a>About</a><a>Probate</a><a>Process</a><a>FAQ</a><a>Contact Us</a><a>Blog</a>
  </nav>
  <div class="header-phone">
    <span class="phone-ring"><svg width="16" height="16" viewBox="0 0 24 24"><path fill="#e8a20c" d="M6.6 10.8a15 15 0 0 0 6.6 6.6l2.2-2.2c.3-.3.7-.4 1-.2 1.1.4 2.3.6 3.6.6.6 0 1 .4 1 1V20c0 .6-.4 1-1 1A17 17 0 0 1 3 4c0-.6.4-1 1-1h3.5c.6 0 1 .4 1 1 0 1.3.2 2.5.6 3.6.1.3 0 .7-.2 1z"/></svg></span>
    1.800.555.0199
  </div>
</header>

<section class="hero" role="img" aria-label="Evening city skyline photograph">
  <div class="hero-text hero-sub">Helping Californians deal with loss with</div>
  <h1 class="hero-text hero-title">DIGNITY &amp; UNDERSTATING</h1>
  <a class="btn">Learn More Info</a>
  <span class="hero-arrow" style="left:96px"><svg width="10" height="14" viewBox="0 0 10 14"><path d="M8 1 2 7l6 6" fill="none" stroke="#333" stroke-width="2"/></svg></span>
  <span class="hero-arrow" style="left:1070px"><svg width="10" height="14" viewBox="0 0 10 14"><path d="m2 1 6 6-6 6" fill="none" stroke="#333" stroke-width="2"/></svg></span>
</section>

<section class="steps">
  <h2>STEPS IN PROBATE</h2>
  <div class="step-divider" style="left:432px"></div>
  <div class="step-divider" style="left:765px"></div>
  <div class="step" style="left:116px">
    <svg width="134" height="150" viewBox="0 0 134 150"><polygon points="67,3 130,39 130,111 67,147 4,111 4,39" fill="none" stroke="#fff" stroke-width="2"/><g fill="#fff"><circle cx="67" cy="58" r="10"/><circle cx="46" cy="64" r="8"/><circle cx="88" cy="64" r="8"/><path d="M50 96c0-14 8-22 17-22s17 8 17 22z"/><path d="M32 96c0-11 6-18 14-18 4 0 7 2 9 4-4 4-6 9-6 14z"/><path d="M102 96c0-11-6-18-14-18-4 0-7 2-9 4 4 4 6 9 6 14z"/></g></svg>
    <h3>Gather</h3><div class="bar"></div>
    <p>Aliquip ex ea commodo consequat. Duis aute irure dolor reprehenderit in voluptate velit esse.</p>
  </div>
  <div class="step" style="left:449px">
    <svg width="134" height="150" viewBox="0 0 134 150"><polygon points="67,3 130,39 130,111 67,147 4,111 4,39" fill="none" stroke="#fff" stroke-width="2"/><g fill="#fff"><polygon points="67,44 100,60 34,60"/><rect x="36" y="63" width="62" height="5"/><rect x="41" y="71" width="7" height="24"/><rect x="54" y="71" width="7" height="24"/><rect x="73" y="71" width="7" height="24"/><rect x="86" y="71" width="7" height="24"/><rect x="34" y="98" width="66" height="6"/></g></svg>
    <h3>Implement</h3><div class="bar"></div>
    <p>Aliquip ex ea commodo consequat. Duis aute irure dolor reprehenderit in voluptate velit esse.</p>
  </div>
  <div class="step" style="left:781px">
    <svg width="134" height="150" viewBox="0 0 134 150"><polygon points="67,3 130,39 130,111 67,147 4,111 4,39" fill="none" stroke="#fff" stroke-width="2"/><g fill="#fff"><path d="M58 44l14 8-16 28-10-6z"/><path d="M46 76l10 6-9 14-4-2z"/></g><path d="M72 100c6-10 12-4 8 2s10 4 14-6" fill="none" stroke="#fff" stroke-width="2.5"/></svg>
    <h3>Close</h3><div class="bar"></div>
    <p>Aliquip ex ea commodo consequat. Duis aute irure dolor reprehenderit in voluptate velit esse.</p>
  </div>
</section>

<section class="why">
  <div class="why-photo" role="img" aria-label="Photograph of a smiling man in a dark suit with arms crossed"></div>
  <h2>WHY CHOOSE US</h2>
  <div class="reason" style="top:189px">
    <svg class="icon" width="44" height="44" viewBox="0 0 44 44"><rect x="6" y="8" width="26" height="32" fill="none" stroke="#e8a20c" stroke-width="3"/><path d="M12 18h14M12 25h14M12 32h9" stroke="#e8a20c" stroke-width="2.5"/><path d="M36 4l5 5-16 16-6 1 1-6z" fill="#e8a20c"/></svg>
    <h4>Excepteur Sint Aoccaecat</h4>
    <p>Aliquip ex ea commodo consequat. Duis aute irure dolor in reprehenderit in voluptate velit esse cillum dolore eu fugiat nulla pariatur. Excepteur sint occaecat cupidatat non proident sunt in culpa qui officia deserunt.</p>
  </div>
  <div class="reason" style="top:326px">
    <svg class="icon" width="44" height="44" viewBox="0 0 44 44"><path d="M22 5c8 0 12 7 12 14v9l5 6H5l5-6v-9C10 12 14 5 22 5z" fill="#e8a20c"/><circle cx="22" cy="38" r="4" fill="#e8a20c"/></svg>
    <h4>Excepteur Sint Aoccaecat</h4>
    <p>Aliquip ex ea commodo consequat. Duis aute irure dolor in reprehenderit in voluptate velit esse cillum dolore eu fugiat nulla pariatur. Excepteur sint occaecat cupidatat non proident sunt in culpa qui officia deserunt.</p>
  </div>
  <div class="reason" style="top:462px">
    <svg class="icon" width="48" height="44" viewBox="0 0 48 44"><path d="M2 16l10-6 10 4 6-2 10 2 8 4-6 12-8 6-6 2-10-6-8-6z" fill="#e8a20c"/><path d="M14 26l6 4M18 22l8 6M24 20l8 6" stroke="#fff" stroke-width="2"/></svg>
    <h4>Excepteur Sint Aoccaecat</h4>
    <p>Aliquip ex ea commodo consequat. Duis aute irure dolor in reprehenderit in voluptate velit esse cillum dolore eu fugiat nulla pariatur. Excepteur sint occaecat cupidatat non proident sunt in culpa qui officia deserunt.</p>
  </div>
</section>

<section class="fee" role="img" aria-label="Photograph of a family with a baby at home, darkened">
  <h2>FLAT-FEE PRICE &amp; SAVINGS</h2>
  <p style="top:140px">Aliquip ex ea commodo consequat. Duis aute irure dolor in reprehenderit in voluptate velit esse cillum dolore eu fugiat nulla pariatur. Excepteur sint occaecat cupidatat non proident, sunt in culpa qui officia deserunt mollit anim id est laborum.</p>
  <p style="top:220px">Aliquip ex ea commodo consequat. Duis aute irure dolor in reprehenderit in voluptate velit esse cillum dolore eu fugiat nulla pariatur. Excepteur sint.</p>
  <a class="btn">Contact Us</a>
</section>

<section class="faq">
  <h2>YOU HAVE QUESTIONS</h2>
  <div class="q open" style="left:132px;top:134px;width:460px;height:100px">
    <div class="qi"><svg width="22" height="22" viewBox="0 0 22 22"><circle cx="11" cy="11" r="9" fill="none" stroke="#fff" stroke-width="2"/><text x="11" y="15.5" text-anchor="middle" font-family="Lato,sans-serif" font-weight="700" font-size="12" fill="#fff">?</text></svg></div>
    <div class="qb"><div class="qt">Adipisci velit, sed quia non numquam eius modi tempora ipsum</div><div class="qa">Aliquip ex ea commodo consequat. Duis aute irure dolor in reprehenderit in voluptate velit esse cillum dolore eu fugiat nulla pariatur...</div>
    <svg class="pm" width="12" height="12" viewBox="0 0 12 12"><rect x=".5" y=".5" width="11" height="11" fill="none" stroke="#999"/><path d="M3 6h6" stroke="#999"/></svg></div>
  </div>
  <div class="q" style="left:132px;top:246px;width:460px;height:45px">
    <div class="qi"><svg width="22" height="22" viewBox="0 0 22 22"><circle cx="11" cy="11" r="9" fill="none" stroke="#fff" stroke-width="2"/><text x="11" y="15.5" text-anchor="middle" font-family="Lato,sans-serif" font-weight="700" font-size="12" fill="#fff">?</text></svg></div>
    <div class="qb"><div class="qt">Adipisci velit, sed quia non numquam eius modi tempora ipsum</div>
    <svg class="pm" width="12" height="12" viewBox="0 0 12 12"><rect x=".5" y=".5" width="11" height="11" fill="none" stroke="#999"/><path d="M3 6h6M6 3v6" stroke="#999"/></svg></div>
  </div>
  <div class="q" style="left:606px;top:134px;width:460px;height:45px">
    <div class="qi"><svg width="22" height="22" viewBox="0 0 22 22"><circle cx="11" cy="11" r="9" fill="none" stroke="#fff" stroke-width="2"/><text x="11" y="15.5" text-anchor="middle" font-family="Lato,sans-serif" font-weight="700" font-size="12" fill="#fff">?</text></svg></div>
    <div class="qb"><div class="qt">Adipisci velit, sed quia non numquam eius modi tempora ipsum</div>
    <svg class="pm" width="12" height="12" viewBox="0 0 12 12"><rect x=".5" y=".5" width="11" height="11" fill="none" stroke="#999"/><path d="M3 6h6M6 3v6" stroke="#999"/></svg></div>
  </div>
  <div class="q" style="left:606px;top:190px;width:460px;height:45px">
    <div class="qi"><svg width="22" height="22" viewBox="0 0 22 22"><circle cx="11" cy="11" r="9" fill="none" stroke="#fff" stroke-width="2"/><text x="11" y="15.5" text-anchor="middle" font-family="Lato,sans-serif" font-weight="700" font-size="12" fill="#fff">?</text></svg></div>
    <div class="qb"><div class="qt">Adipisci velit, sed quia non numquam eius modi tempora ipsum</div>
    <svg class="pm" width="12" height="12" viewBox="0 0 12 12"><rect x=".5" y=".5" width="11" height="11" fill="none" stroke="#999"/><path d="M3 6h6M6 3v6" stroke="#999"/></svg></div>
  </div>
  <div class="q" style="left:606px;top:246px;width:460px;height:45px">
    <div class="qi"><svg width="22" height="22" viewBox="0 0 22 22"><circle cx="11" cy="11" r="9" fill="none" stroke="#fff" stroke-width="2"/><text x="11" y="15.5" text-anchor="middle" font-family="Lato,sans-serif" font-weight="700" font-size="12" fill="#fff">?</text></svg></div>
    <div class="qb"><div class="qt">Adipisci velit, sed quia non numquam eius modi tempora ipsum</div>
    <svg class="pm" width="12" height="12" viewBox="0 0 12 12"><rect x=".5" y=".5" width="11" height="11" fill="none" stroke="#999"/><path d="M3 6h6M6 3v6" stroke="#999"/></svg></div>
  </div>
</section>

<section class="know">
  <h2>GET TO KNOW US</h2>
  <h3 style="left:545px;top:170px;width:200px;text-align:right">What We Do</h3>
  <p style="left:132px;top:212px;width:613px;text-align:right">Accusantium doloremque laudantium, totam rem aperiam, eaque ipsa quae ab illo inventore veritatis quasi architecto beatae vitae dicta sunt explicabo. Nemo enim ipsam voluptatem quia voluptas sit aspernatur aut odit aut fugit, sed quia consequuntur magni dolores aliquip ex ea commodo eos qui ratione cupidatat non proident...</p>
  <a class="btn" style="left:642px;top:289px;width:103px;height:37px">Read More</a>
  <div class="circle" style="left:842px;top:147px"><div role="img" aria-label="Photograph of hands signing paperwork" style="background:linear-gradient(135deg,#f3f6f9,#c9d4de 60%,#8ea3b6)"></div></div>

  <div class="circle" style="left:141px;top:365px"><div role="img" aria-label="Photograph of a smiling couple reviewing papers" style="background:linear-gradient(135deg,#e9eef3,#b7c4d2 55%,#5d7ca0)"></div></div>
  <h3 style="left:460px;top:400px">Who We Are</h3>
  <p style="left:460px;top:440px;width:610px">Accusantium doloremque laudantium, totam rem aperiam, eaque ipsa quae ab illo inventore veritatis quasi architecto beatae vitae dicta sunt explicabo. Nemo enim ipsam voluptatem quia voluptas sit aspernatur aut odit aut fugit, sed quia consequuntur magni dolores aliquip ex ea commodo eos qui ratione cupidatat non proident...</p>
  <a class="btn" style="left:460px;top:512px;width:103px;height:37px">Read More</a>
</section>

<footer class="footer">
  <div class="fcol" style="left:132px">
    <h4>NAVIGATION</h4>
    <ul><li>Home</li><li>About</li><li>Probate</li><li>Process</li><li>FAQ</li><li>Contact Us</li><li>Blog</li></ul>
  </div>
  <div class="fcol" style="left:335px">
    <h4>INFORMATION</h4>
    <ul><li>Terms &amp; Conditions</li><li>Privacy Policy</li><li>Site Map</li><li>Disclaimer</li><li>More Information</li><li>Document Assistants</li></ul>
  </div>
  <div class="fcol" style="left:562px;width:240px">
    <h4>NEWSLETTER</h4>
    <p>Lorem ipsum dolor sit amet, consectetur adipiscing elit, sed do eiusmod...</p>
    <div class="news-input">Enter Email Address</div>
    <a class="btn">Read More</a>
  </div>
  <div class="fcol" style="left:902px;width:170px">
    <h4>CONTACT INFO</h4>
    <div class="contact-row"><svg width="12" height="12" viewBox="0 0 12 12"><rect x="1" y="1" width="10" height="10" rx="1" fill="#fff"/></svg>(555) 014-2290</div>
    <div class="contact-row"><svg width="12" height="12" viewBox="0 0 12 12"><rect x="1" y="2" width="10" height="8" fill="#fff"/></svg>(555) 014-2290</div>
    <div class="contact-row"><svg width="12" height="12" viewBox="0 0 12 12"><rect x="1" y="2.5" width="10" height="7" fill="#fff"/><path d="M1 3l5 4 5-4" fill="none" stroke="#0b63b6"/></svg><span style="text-decoration:underline">info@velmarhollow.com</span></div>
    <div class="contact-row"><svg width="12" height="14" viewBox="0 0 12 14"><path d="M6 1a4 4 0 0 1 4 4c0 3-4 8-4 8S2 8 2 5a4 4 0 0 1 4-4z" fill="#fff"/></svg><span>#2868 Lorem ipsum dolor sit amet, consectetur</span></div>
  </div>
</footer>
<div class="bottom-bar">
  <div class="copy">Copyrights © 2017, velmarhollow | All rights reserved.</div>
  <div class="follow">Follow Us <span class="social"></span><span class="social"></span><span class="social"></span><span class="social"></span><span class="social"></span></div>
</div>

</body>
</html>
```